Exciting new website for concierge aesthetic company

Simple, elegant, fresh design for female owned concierge aesthetic company, catering to both men and women ages 30-60. We would like a home page with an exciting catch phrase, a brief description of the company and a section to fill out an appointment request that includes a section for a referral. Please also have a book appointment link in the header of all pages that will link back to booking information form on home page. Separate pages to include:
- Services = 3 different services. Each service stating the name of the service and then providing a brief description. 3 services are "Private Session" for 1 client, "Group Session" for 2-5 clients, "Party" for 6+ clients. Will provide service descriptions text later. Item at bottom of page to allow description of how to "Host a Party".
- Products = 4 different product lines. Will provide pictures of product, brief description and link to manufacturer's website.
- Stories = brief client reviews to include before and after photos
- About us = Personal picture with brief description of owner's fun, exciting and family focussed lifestyle.
*Our domain is registered with varnix and we be using varnix for website hosting.

Target Market(s)

30-60 year old men and women, but mostly women

Industry/Entity Type

beauty and aesthetics

Coding

Coded - Design and coding required

Number of Pages Required

5+ page

Font styles to use
Sans Serif
Script

Colors
59FF00
82FF00
B8FF75
E3FFCB
F4FFEA
FFC000
F8CF3A
FAE287
FDF2CF
FEFAEE
F0912C
F2A743
F7CA91
FBE8D2
FDF5EE
E54698
E96AAD
F1A4CE
F9D9EA
FCEFF6

Requirements
Must have
• coded for varnix
Should not have
• corny pictures. No needles in pictures or graphics. No medical office or medical chair in pictures.

```html
<!DOCTYPE html>
<html lang="en">
<head>
<meta charset="utf-8">
<title>Glow Muse – Homepage Colour Options</title>
<link href="https://fonts.googleapis.com/css2?family=Dancing+Script:wght@400;600&family=Montserrat:wght@400;500&display=swap" rel="stylesheet">
<style>
  :root{
    --board-a:#EE93C4;
    --board-b:#F5A89A;
    --board-c:#FBC584;
    --peach:#FBC98C;
    --cream:#F8F4E2;
    --hero:#D4D9E1;
    --pink:#E54698;
    --pink-soft:#E96AAD;
    --orange:#F0912C;
    --coral:#EF6A4A;
    --ink:#3A2A2A;
    --muted:#5E4A4A;
    --dark:#242424;
    --white:#FFFFFF;
    --script:"Dancing Script", cursive;
    --sans:"Montserrat", sans-serif;
  }
  *{box-sizing:border-box;margin:0;padding:0}
  html,body{width:1200px;height:1171px;overflow:hidden}
  body{background:linear-gradient(90deg,var(--board-a),var(--board-b) 50%,var(--board-c));position:relative;font-family:var(--sans);color:var(--ink)}
  .panel{position:absolute;top:27px;width:359px;height:1117px;overflow:hidden;background:var(--section);box-shadow:0 4px 14px rgba(120,40,60,.18)}
  .panel--peach{--section:var(--peach);--header:#FCC58A;left:25px}
  .panel--cream{--section:var(--cream);--header:#F8F3E0}
  .panel--b{left:420px}
  .panel--c{left:815px}
  .panel > *{position:absolute}
  .backdrop{left:0;top:0;width:359px;height:1117px}

  /* header */
  .site-header{left:0;top:0;width:359px;height:32px;background:var(--header)}
  .brand{position:absolute;left:34px;top:6px;display:flex;align-items:center;gap:4px}
  .brand-dot{width:14px;height:14px;border-radius:50%;border:1px solid var(--coral)}
  .brand-name{font-family:var(--script);font-weight:600;font-size:13px;color:var(--orange);line-height:1}
  .brand-name small{display:block;font-family:var(--sans);font-size:2.6px;letter-spacing:1.4px;font-weight:400;margin-top:2px}
  .nav{position:absolute;left:134px;top:13px;display:flex;gap:11px;font-size:4.8px;color:var(--ink)}
  .book-btn{position:absolute;left:272px;top:9px;width:54px;height:16px;background:var(--pink);color:var(--white);font-family:var(--script);font-size:6px;display:flex;align-items:center;justify-content:center;border-radius:6px 0 6px 0}

  /* hero */
  .hero-title{left:33px;top:86px;font-family:var(--script);font-size:31px;color:var(--orange);font-weight:400;line-height:1}
  .hero-sub{left:34px;top:124px;font-size:5px;letter-spacing:3.7px;color:var(--coral)}
  .cta{left:79px;top:145px;width:41px;height:15px;background:var(--pink);color:var(--white);font-family:var(--script);font-size:6px;display:flex;align-items:center;justify-content:center;border-radius:6px 0 6px 0}
  .arrow{top:133px;width:8px;height:12px}
  .arrow--prev{left:13px}
  .arrow--next{left:336px}
  .dots{left:173px;top:208px;display:flex;gap:2px}
  .dots i{width:3px;height:3px;border-radius:50%;background:#B8B0B0;display:block}
  .dots i.on{background:var(--orange)}

  .section-title{left:0;width:359px;text-align:center;font-family:var(--script);font-size:12px;font-weight:400;color:var(--coral);line-height:1}
  .section-title--products{top:276px}
  .section-title--services{top:680px}
  .section-title--stories{top:850px}

  /* products */
  .products{left:34px;top:298px;display:flex;gap:6px}
  .product{width:69px;height:113px;background:var(--white);box-shadow:0 1px 4px rgba(0,0,0,.14);padding:3px;text-align:center;position:relative}
  .product .thumb{height:49px}
  .thumb--spa{background:linear-gradient(160deg,#F1EEEA 0%,#D8D2CB 35%,#B9A08E 55%,#EDE7E1 75%,#CFC6BC 100%)}
  .thumb--calm{background:linear-gradient(200deg,#E9E2DD 0%,#D6B8A6 40%,#F4F1EF 60%,#C9C4C2 100%)}
  .thumb--consult{background:linear-gradient(100deg,#8FB5B6 0%,#C7D6D5 30%,#D9B5A0 55%,#3E3533 75%,#E6EEEE 100%)}
  .thumb--towel{background:linear-gradient(135deg,#F7F3EE 0%,#E9D6C2 40%,#D9A985 60%,#F4EDE6 100%)}
  .product h3{font-family:var(--script);font-weight:400;font-size:6.4px;margin-top:6px;color:var(--ink)}
  .product p{font-family:var(--script);font-size:4.4px;line-height:1.5;margin:4px 3px 0;color:var(--muted)}
  .product .more{position:absolute;left:15px;bottom:6px;width:39px;height:12px;border:.7px solid var(--pink);border-radius:5px 0 5px 0;font-family:var(--script);font-size:5.4px;color:var(--pink);display:flex;align-items:center;justify-content:center}
  .product--active{background:var(--pink)}
  .product--active h3,.product--active p{color:var(--white)}
  .product--active .more{border-color:var(--white);color:var(--white)}

  /* about */
  .about-photo{left:47px;top:488px;width:126px;height:126px;border-radius:50%;background:radial-gradient(circle at 50% 42%,#EAD9CE 0%,#D7BBA9 22%,#A9A6AC 48%,#8C8D94 75%,#6F7079 100%);box-shadow:2px 4px 0 var(--orange)}
  .about-title{left:205px;top:478px;font-family:var(--script);font-weight:400;font-size:12px;color:var(--coral)}
  .about-copy{left:205px;top:496px;width:122px;font-family:var(--script);font-size:4.7px;line-height:7.7px;color:var(--ink);text-align:justify}
  .about-btn{left:205px;top:589px;width:41px;height:15px;background:var(--pink);color:var(--white);font-family:var(--script);font-size:6px;display:flex;align-items:center;justify-content:center;border-radius:6px 0 6px 0}

  /* services */
  .services{left:67px;top:708px;display:flex;gap:11px}
  .service{width:68px;height:71px;background:var(--white);border:.7px solid var(--orange);text-align:center;padding-top:7px}
  .service svg{display:block;margin:0 auto;height:24px}
  .service h3{font-family:var(--script);font-weight:400;font-size:6.4px;margin-top:6px}
  .service p{font-family:var(--script);font-size:3.9px;line-height:1.5;margin:3px 5px 0;color:var(--muted)}

  /* stories */
  .story{top:877px;width:141px;height:76px;border-radius:6px 0 6px 0}
  .story--one{left:34px;background:linear-gradient(90deg,#E9E8E6 0%,#D9C2B2 30%,#C79A82 48%,#F2F1EF 50%,#D8BCA8 70%,#EDEDEC 100%)}
  .story--two{left:185px;background:linear-gradient(90deg,#C9A894 0%,#D9BFAE 30%,#B58E78 49%,#F7F5F3 50%,#E4CBBA 75%,#D3B4A0 100%)}

  /* footer */
  .foot-brand{left:34px;top:1060px;font-family:var(--script);font-weight:600;font-size:17px;color:var(--orange);line-height:1}
  .foot-brand small{display:block;font-family:var(--sans);font-weight:400;font-size:2.8px;letter-spacing:1.6px;margin-top:3px}
  .foot-col{top:1029px;color:var(--white)}
  .foot-col h4{font-family:var(--script);font-weight:400;font-size:8px;margin-bottom:5px}
  .foot-col ul{list-style:none}
  .foot-col li{font-family:var(--script);font-size:4.6px;line-height:7.7px}
  .foot-col--links{left:146px}
  .foot-col--service{left:218px}
  .foot-col--terms{left:285px}
  .foot-rule{left:34px;top:1089px;width:291px;height:.5px;background:#555}
  .copyright{left:34px;top:1097px;font-family:var(--script);font-size:4.6px;color:var(--white)}
  .social{left:291px;top:1098px;display:flex;gap:5px}
  .social i{display:block;width:5px;height:5px;border-radius:50%;background:var(--orange)}
</style>
</head>
<body>

<svg width="0" height="0" style="position:absolute" aria-hidden="true">
  <defs>
    <linearGradient id="wave" x1="0" x2="1">
      <stop offset="0" stop-color="#E54698"/>
      <stop offset=".55" stop-color="#EF5F6A"/>
      <stop offset="1" stop-color="#F0912C"/>
    </linearGradient>
    <radialGradient id="portrait" cx=".6" cy=".45" r=".65">
      <stop offset="0" stop-color="#F0D3C0"/>
      <stop offset=".45" stop-color="#E2B79E"/>
      <stop offset=".8" stop-color="#C89C84" stop-opacity=".6"/>
      <stop offset="1" stop-color="#D4D9E1" stop-opacity="0"/>
    </radialGradient>
    <linearGradient id="spa" x1="0" x2="0" y1="0" y2="1">
      <stop offset="0" stop-color="#FFFFFF" stop-opacity=".25"/>
      <stop offset="1" stop-color="#E8D8B8" stop-opacity=".35"/>
    </linearGradient>
  </defs>
</svg>

<!-- ============ Option A: peach ============ -->
<section class="panel panel--peach">
  <svg class="backdrop" viewBox="0 0 359 1117" aria-hidden="true">
    <path d="M0 32H359V215C300 222 230 238 150 246C90 252 40 246 0 231Z" fill="var(--hero)"/>
    <rect x="170" y="32" width="189" height="210" fill="url(#portrait)" role="img" aria-label="Portrait of a smiling woman touching her cheek"/>
    <path d="M0 231C40 246 90 252 150 246C230 238 300 222 359 215L359 212C300 219 230 235 150 243C90 249 40 243 0 228Z" fill="url(#wave)"/>
    <path d="M0 452C30 462 60 467 100 462C180 450 250 428 300 432C330 434 350 442 359 452L359 449C350 438 330 430 300 428C250 424 180 446 100 459C60 464 30 459 0 449Z" fill="url(#wave)"/>
    <path d="M0 637C30 648 55 654 95 650C170 640 240 616 290 619C325 621 345 627 359 632L359 629C345 623 325 617 290 615C240 612 170 636 95 647C55 651 30 645 0 634Z" fill="url(#wave)"/>
    <path d="M0 816C30 826 60 832 100 829C180 820 250 798 300 801C330 803 350 808 359 813L359 810C350 804 330 799 300 797C250 794 180 816 100 826C60 829 30 823 0 813Z" fill="url(#wave)"/>
    <path d="M0 830C60 835 140 822 220 808C290 798 340 806 359 815V1000H0Z" fill="url(#spa)" role="img" aria-label="Soft blurred spa interior"/>
    <path d="M0 1002C70 996 150 996 220 988C280 980 330 970 359 962V1117H0Z" fill="var(--dark)"/>
  </svg>

  <header class="site-header">
    <div class="brand"><span class="brand-dot"></span><div class="brand-name">Glow Muse<small>CONCIERGE AESTHETICS</small></div></div>
    <nav class="nav"><span>Home</span><span>About</span><span>Services</span><span>Products</span><span>Stories</span></nav>
    <div class="book-btn">Book Appointment</div>
  </header>

  <h1 class="hero-title">Glow Muse</h1>
  <div class="hero-sub">CONCIERGE AESTHETICS</div>
  <div class="cta">Get Started</div>
  <svg class="arrow arrow--prev" viewBox="0 0 8 12" aria-hidden="true"><path d="M6 1L2 6L6 11" fill="none" stroke="#fff" stroke-width="1.2"/></svg>
  <svg class="arrow arrow--next" viewBox="0 0 8 12" aria-hidden="true"><path d="M2 1L6 6L2 11" fill="none" stroke="var(--orange)" stroke-width="1.4"/></svg>
  <div class="dots"><i></i><i class="on"></i><i></i></div>

  <h2 class="section-title section-title--products">Our Products</h2>
  <div class="products">
    <article class="product"><div class="thumb thumb--spa" role="img" aria-label="Client receiving a facial treatment"></div><h3>Lumeve</h3><p>First &amp; only formula made exclusively for aesthetics!</p><div class="more">Learn More</div></article>
    <article class="product product--active"><div class="thumb thumb--calm" role="img" aria-label="Relaxed client during treatment"></div><h3>Smoothe</h3><p>Still you. With fewer lines!</p><div class="more">Learn More</div></article>
    <article class="product"><div class="thumb thumb--consult" role="img" aria-label="Woman during a skin consultation"></div><h3>Purelle</h3><p>PURE. For a reason. And the reason is you.</p><div class="more">Learn More</div></article>
    <article class="product"><div class="thumb thumb--towel" role="img" aria-label="Client relaxing with a towel wrap"></div><h3>Lorem ipsum dolor</h3><p>Lorem ipsum dolor sit amet, consectetur adipiscing elit, sed aliqua.</p><div class="more">Learn More</div></article>
  </div>

  <div class="about-photo" role="img" aria-label="Portrait of a woman with gloved hands framing her face"></div>
  <h2 class="about-title">About Us</h2>
  <p class="about-copy">How often do we put ourselves last, giving all we have to our families and careers? As a fellow team mom, family coordinator and career driven woman, I quickly realized that we have a right to self care while enjoying our active lifestyles! As a Physician Assistant with over nine years of experience, I saw a fit for my passion and experience to allow people to live their best life and look good doing it! My three boys and husband fill my life with wonderful joy. We are an active family, finding adventure on the football field, ski slopes and mountain bike trails. I find rejuvenation in running, coffee and wine. Excited to hear your story!</p>
  <div class="about-btn">Learn More</div>

  <h2 class="section-title section-title--services">Our Services</h2>
  <div class="services">
    <article class="service">
      <svg viewBox="0 0 24 24" aria-hidden="true"><circle cx="12" cy="7" r="4" fill="none" stroke="var(--pink)" stroke-width="1"/><path d="M4 22C4 15 8 13 12 13S20 15 20 22Z" fill="none" stroke="var(--pink)" stroke-width="1"/></svg>
      <h3>Private Session</h3><p>The essence of concierge service! Schedule the time and place most convenient for you.</p>
    </article>
    <article class="service">
      <svg viewBox="0 0 36 24" aria-hidden="true" style="width:36px"><g fill="none" stroke="var(--pink)" stroke-width="1"><circle cx="9" cy="8" r="3"/><circle cx="18" cy="6" r="3.4"/><circle cx="27" cy="8" r="3"/><path d="M3 20C3 14 6 13 9 13S15 14 15 20Z"/><path d="M11 20C11 13 14 11 18 11S25 13 25 20Z"/><path d="M21 20C21 14 24 13 27 13S33 14 33 20Z"/></g></svg>
      <h3>Group Session</h3><p>Bring together family, friends and coworkers. Both the personal touch with reduced pricing!</p>
    </article>
    <article class="service">
      <svg viewBox="0 0 36 24" aria-hidden="true" style="width:36px"><g fill="none" stroke="var(--pink)" stroke-width="1"><circle cx="12" cy="4" r="2.4"/><circle cx="18" cy="3" r="2.4"/><circle cx="24" cy="4" r="2.4"/><circle cx="8" cy="11" r="2.6"/><circle cx="18" cy="10" r="2.8"/><circle cx="28" cy="11" r="2.6"/><path d="M3 22C3 16 5 15 8 15S13 16 13 22Z"/><path d="M12 22C12 15 15 14 18 14S24 15 24 22Z"/><path d="M23 22C23 16 25 15 28 15S33 16 33 22Z"/></g></svg>
      <h3>Glow Party</h3><p>Enjoy time with six or more for wine, hors d'oeuvres, best pricing and host credits!</p>
    </article>
  </div>

  <h2 class="section-title section-title--stories">Our Stories</h2>
  <div class="story story--one" role="img" aria-label="Before and after treatment comparison"></div>
  <div class="story story--two" role="img" aria-label="Before and after close-up of eye area"></div>

  <div class="foot-brand">Glow Muse<small>CONCIERGE AESTHETICS</small></div>
  <div class="foot-col foot-col--links"><h4>Quick Links</h4><ul><li>Home</li><li>About</li><li>Services</li><li>Products</li><li>Stories</li></ul></div>
  <div class="foot-col foot-col--service"><h4>Service</h4><ul><li>Private Session</li><li>Group Session</li><li>Party</li></ul></div>
  <div class="foot-col foot-col--terms"><h4>Conditions</h4><ul><li>Delivery</li><li>Terms of Conditions</li><li>Privacy policy</li></ul></div>
  <div class="foot-rule"></div>
  <div class="copyright">Copyrights 2022 Glow Muse &nbsp;|&nbsp; All Rights Reserved</div>
  <div class="social"><i></i><i></i><i></i><i></i></div>
</section>

<!-- ============ Option B: cream ============ -->
<section class="panel panel--cream panel--b">
  <svg class="backdrop" viewBox="0 0 359 1117" aria-hidden="true">
    <path d="M0 32H359V215C300 222 230 238 150 246C90 252 40 246 0 231Z" fill="var(--hero)"/>
    <rect x="165" y="32" width="194" height="210" fill="url(#portrait)" role="img" aria-label="Portrait of a woman with long hair touching her jaw"/>
    <path d="M0 231C40 246 90 252 150 246C230 238 300 222 359 215L359 212C300 219 230 235 150 243C90 249 40 243 0 228Z" fill="url(#wave)"/>
    <path d="M0 452C30 462 60 467 100 462C180 450 250 428 300 432C330 434 350 442 359 452L359 449C350 438 330 430 300 428C250 424 180 446 100 459C60 464 30 459 0 449Z" fill="url(#wave)"/>
    <path d="M0 637C30 648 55 654 95 650C170 640 240 616 290 619C325 621 345 627 359 632L359 629C345 623 325 617 290 615C240 612 170 636 95 647C55 651 30 645 0 634Z" fill="url(#wave)"/>
    <path d="M0 816C30 826 60 832 100 829C180 820 250 798 300 801C330 803 350 808 359 813L359 810C350 804 330 799 300 797C250 794 180 816 100 826C60 829 30 823 0 813Z" fill="url(#wave)"/>
    <path d="M0 830C60 835 140 822 220 808C290 798 340 806 359 815V1000H0Z" fill="url(#spa)" role="img" aria-label="Soft blurred spa interior"/>
    <path d="M0 1002C70 996 150 996 220 988C280 980 330 970 359 962V1117H0Z" fill="var(--dark)"/>
  </svg>

  <header class="site-header">
    <div class="brand"><span class="brand-dot"></span><div class="brand-name">Glow Muse<small>CONCIERGE AESTHETICS</small></div></div>
    <nav class="nav"><span>Home</span><span>About</span><span>Services</span><span>Products</span><span>Stories</span></nav>
    <div class="book-btn">Book Appointment</div>
  </header>

  <h1 class="hero-title">Glow Muse</h1>
  <div class="hero-sub">CONCIERGE AESTHETICS</div>
  <div class="cta">Get Started</div>
  <svg class="arrow arrow--prev" viewBox="0 0 8 12" aria-hidden="true"><path d="M6 1L2 6L6 11" fill="none" stroke="#fff" stroke-width="1.2"/></svg>
  <svg class="arrow arrow--next" viewBox="0 0 8 12" aria-hidden="true"><path d="M2 1L6 6L2 11" fill="none" stroke="var(--orange)" stroke-width="1.4"/></svg>
  <div class="dots"><i></i><i class="on"></i><i></i></div>

  <h2 class="section-title section-title--products">Our Products</h2>
  <div class="products">
    <article class="product"><div class="thumb thumb--spa" role="img" aria-label="Client receiving a facial treatment"></div><h3>Lumeve</h3><p>First &amp; only formula made exclusively for aesthetics!</p><div class="more">Learn More</div></article>
    <article class="product product--active"><div class="thumb thumb--calm" role="img" aria-label="Relaxed client during treatment"></div><h3>Smoothe</h3><p>Still you. With fewer lines!</p><div class="more">Learn More</div></article>
    <article class="product"><div class="thumb thumb--consult" role="img" aria-label="Woman during a skin consultation"></div><h3>Purelle</h3><p>PURE. For a reason. And the reason is you.</p><div class="more">Learn More</div></article>
    <article class="product"><div class="thumb thumb--towel" role="img" aria-label="Client relaxing with a towel wrap"></div><h3>Lorem ipsum dolor</h3><p>Lorem ipsum dolor sit amet, consectetur adipiscing elit, sed aliqua.</p><div class="more">Learn More</div></article>
  </div>

  <div class="about-photo" role="img" aria-label="Portrait of a woman with gloved hands framing her face"></div>
  <h2 class="about-title">About Us</h2>
  <p class="about-copy">How often do we put ourselves last, giving all we have to our families and careers? As a fellow team mom, family coordinator and career driven woman, I quickly realized that we have a right to self care while enjoying our active lifestyles! As a Physician Assistant with over nine years of experience, I saw a fit for my passion and experience to allow people to live their best life and look good doing it! My three boys and husband fill my life with wonderful joy. We are an active family, finding adventure on the football field, ski slopes and mountain bike trails. I find rejuvenation in running, coffee and wine. Excited to hear your story!</p>
  <div class="about-btn">Learn More</div>

  <h2 class="section-title section-title--services">Our Services</h2>
  <div class="services">
    <article class="service">
      <svg viewBox="0 0 24 24" aria-hidden="true"><circle cx="12" cy="7" r="4" fill="none" stroke="var(--pink)" stroke-width="1"/><path d="M4 22C4 15 8 13 12 13S20 15 20 22Z" fill="none" stroke="var(--pink)" stroke-width="1"/></svg>
      <h3>Private Session</h3><p>The essence of concierge service! Schedule the time and place most convenient for you.</p>
    </article>
    <article class="service">
      <svg viewBox="0 0 36 24" aria-hidden="true" style="width:36px"><g fill="none" stroke="var(--pink)" stroke-width="1"><circle cx="9" cy="8" r="3"/><circle cx="18" cy="6" r="3.4"/><circle cx="27" cy="8" r="3"/><path d="M3 20C3 14 6 13 9 13S15 14 15 20Z"/><path d="M11 20C11 13 14 11 18 11S25 13 25 20Z"/><path d="M21 20C21 14 24 13 27 13S33 14 33 20Z"/></g></svg>
      <h3>Group Session</h3><p>Bring together family, friends and coworkers. Both the personal touch with reduced pricing!</p>
    </article>
    <article class="service">
      <svg viewBox="0 0 36 24" aria-hidden="true" style="width:36px"><g fill="none" stroke="var(--pink)" stroke-width="1"><circle cx="12" cy="4" r="2.4"/><circle cx="18" cy="3" r="2.4"/><circle cx="24" cy="4" r="2.4"/><circle cx="8" cy="11" r="2.6"/><circle cx="18" cy="10" r="2.8"/><circle cx="28" cy="11" r="2.6"/><path d="M3 22C3 16 5 15 8 15S13 16 13 22Z"/><path d="M12 22C12 15 15 14 18 14S24 15 24 22Z"/><path d="M23 22C23 16 25 15 28 15S33 16 33 22Z"/></g></svg>
      <h3>Glow Party</h3><p>Enjoy time with six or more for wine, hors d'oeuvres, best pricing and host credits!</p>
    </article>
  </div>

  <h2 class="section-title section-title--stories">Our Stories</h2>
  <div class="story story--one" role="img" aria-label="Before and after treatment comparison"></div>
  <div class="story story--two" role="img" aria-label="Before and after close-up of eye area"></div>

  <div class="foot-brand">Glow Muse<small>CONCIERGE AESTHETICS</small></div>
  <div class="foot-col foot-col--links"><h4>Quick Links</h4><ul><li>Home</li><li>About</li><li>Services</li><li>Products</li><li>Stories</li></ul></div>
  <div class="foot-col foot-col--service"><h4>Service</h4><ul><li>Private Session</li><li>Group Session</li><li>Party</li></ul></div>
  <div class="foot-col foot-col--terms"><h4>Conditions</h4><ul><li>Delivery</li><li>Terms of Conditions</li><li>Privacy policy</li></ul></div>
  <div class="foot-rule"></div>
  <div class="copyright">Copyrights 2022 Glow Muse &nbsp;|&nbsp; All Rights Reserved</div>
  <div class="social"><i></i><i></i><i></i><i></i></div>
</section>

<!-- ============ Option C: cream ============ -->
<section class="panel panel--cream panel--c">
  <svg class="backdrop" viewBox="0 0 359 1117" aria-hidden="true">
    <path d="M0 32H359V215C300 222 230 238 150 246C90 252 40 246 0 231Z" fill="var(--hero)"/>
    <rect x="160" y="32" width="199" height="210" fill="url(#portrait)" role="img" aria-label="Portrait of a smiling woman with hair tied back"/>
    <path d="M0 231C40 246 90 252 150 246C230 238 300 222 359 215L359 212C300 219 230 235 150 243C90 249 40 243 0 228Z" fill="url(#wave)"/>
    <path d="M0 452C30 462 60 467 100 462C180 450 250 428 300 432C330 434 350 442 359 452L359 449C350 438 330 430 300 428C250 424 180 446 100 459C60 464 30 459 0 449Z" fill="url(#wave)"/>
    <path d="M0 637C30 648 55 654 95 650C170 640 240 616 290 619C325 621 345 627 359 632L359 629C345 623 325 617 290 615C240 612 170 636 95 647C55 651 30 645 0 634Z" fill="url(#wave)"/>
    <path d="M0 816C30 826 60 832 100 829C180 820 250 798 300 801C330 803 350 808 359 813L359 810C350 804 330 799 300 797C250 794 180 816 100 826C60 829 30 823 0 813Z" fill="url(#wave)"/>
    <path d="M0 830C60 835 140 822 220 808C290 798 340 806 359 815V1000H0Z" fill="url(#spa)" role="img" aria-label="Soft blurred spa interior"/>
    <path d="M0 1002C70 996 150 996 220 988C280 980 330 970 359 962V1117H0Z" fill="var(--dark)"/>
  </svg>

  <header class="site-header">
    <div class="brand"><span class="brand-dot"></span><div class="brand-name">Glow Muse<small>CONCIERGE AESTHETICS</small></div></div>
    <nav class="nav"><span>Home</span><span>About</span><span>Services</span><span>Products</span><span>Stories</span></nav>
    <div class="book-btn">Book Appointment</div>
  </header>

  <h1 class="hero-title">Glow Muse</h1>
  <div class="hero-sub">CONCIERGE AESTHETICS</div>
  <div class="cta">Get Started</div>
  <svg class="arrow arrow--prev" viewBox="0 0 8 12" aria-hidden="true"><path d="M6 1L2 6L6 11" fill="none" stroke="#fff" stroke-width="1.2"/></svg>
  <svg class="arrow arrow--next" viewBox="0 0 8 12" aria-hidden="true"><path d="M2 1L6 6L2 11" fill="none" stroke="var(--orange)" stroke-width="1.4"/></svg>
  <div class="dots"><i></i><i class="on"></i><i></i></div>

  <h2 class="section-title section-title--products">Our Products</h2>
  <div class="products">
    <article class="product"><div class="thumb thumb--spa" role="img" aria-label="Client receiving a facial treatment"></div><h3>Lumeve</h3><p>First &amp; only formula made exclusively for aesthetics!</p><div class="more">Learn More</div></article>
    <article class="product product--active"><div class="thumb thumb--calm" role="img" aria-label="Relaxed client during treatment"></div><h3>Smoothe</h3><p>Still you. With fewer lines!</p><div class="more">Learn More</div></article>
    <article class="product"><div class="thumb thumb--consult" role="img" aria-label="Woman during a skin consultation"></div><h3>Purelle</h3><p>PURE. For a reason. And the reason is you.</p><div class="more">Learn More</div></article>
    <article class="product"><div class="thumb thumb--towel" role="img" aria-label="Client relaxing with a towel wrap"></div><h3>Lorem ipsum dolor</h3><p>Lorem ipsum dolor sit amet, consectetur adipiscing elit, sed aliqua.</p><div class="more">Learn More</div></article>
  </div>

  <div class="about-photo" role="img" aria-label="Portrait of a woman with gloved hands framing her face"></div>
  <h2 class="about-title">About Us</h2>
  <p class="about-copy">How often do we put ourselves last, giving all we have to our families and careers? As a fellow team mom, family coordinator and career driven woman, I quickly realized that we have a right to self care while enjoying our active lifestyles! As a Physician Assistant with over nine years of experience, I saw a fit for my passion and experience to allow people to live their best life and look good doing it! My three boys and husband fill my life with wonderful joy. We are an active family, finding adventure on the football field, ski slopes and mountain bike trails. I find rejuvenation in running, coffee and wine. Excited to hear your story!</p>
  <div class="about-btn">Learn More</div>

  <h2 class="section-title section-title--services">Our Services</h2>
  <div class="services">
    <article class="service">
      <svg viewBox="0 0 24 24" aria-hidden="true"><circle cx="12" cy="7" r="4" fill="none" stroke="var(--pink)" stroke-width="1"/><path d="M4 22C4 15 8 13 12 13S20 15 20 22Z" fill="none" stroke="var(--pink)" stroke-width="1"/></svg>
      <h3>Private Session</h3><p>The essence of concierge service! Schedule the time and place most convenient for you.</p>
    </article>
    <article class="service">
      <svg viewBox="0 0 36 24" aria-hidden="true" style="width:36px"><g fill="none" stroke="var(--pink)" stroke-width="1"><circle cx="9" cy="8" r="3"/><circle cx="18" cy="6" r="3.4"/><circle cx="27" cy="8" r="3"/><path d="M3 20C3 14 6 13 9 13S15 14 15 20Z"/><path d="M11 20C11 13 14 11 18 11S25 13 25 20Z"/><path d="M21 20C21 14 24 13 27 13S33 14 33 20Z"/></g></svg>
      <h3>Group Session</h3><p>Bring together family, friends and coworkers. Both the personal touch with reduced pricing!</p>
    </article>
    <article class="service">
      <svg viewBox="0 0 36 24" aria-hidden="true" style="width:36px"><g fill="none" stroke="var(--pink)" stroke-width="1"><circle cx="12" cy="4" r="2.4"/><circle cx="18" cy="3" r="2.4"/><circle cx="24" cy="4" r="2.4"/><circle cx="8" cy="11" r="2.6"/><circle cx="18" cy="10" r="2.8"/><circle cx="28" cy="11" r="2.6"/><path d="M3 22C3 16 5 15 8 15S13 16 13 22Z"/><path d="M12 22C12 15 15 14 18 14S24 15 24 22Z"/><path d="M23 22C23 16 25 15 28 15S33 16 33 22Z"/></g></svg>
      <h3>Glow Party</h3><p>Enjoy time with six or more for wine, hors d'oeuvres, best pricing and host credits!</p>
    </article>
  </div>

  <h2 class="section-title section-title--stories">Our Stories</h2>
  <div class="story story--one" role="img" aria-label="Before and after treatment comparison"></div>
  <div class="story story--two" role="img" aria-label="Before and after close-up of eye area"></div>

  <div class="foot-brand">Glow Muse<small>CONCIERGE AESTHETICS</small></div>
  <div class="foot-col foot-col--links"><h4>Quick Links</h4><ul><li>Home</li><li>About</li><li>Services</li><li>Products</li><li>Stories</li></ul></div>
  <div class="foot-col foot-col--service"><h4>Service</h4><ul><li>Private Session</li><li>Group Session</li><li>Party</li></ul></div>
  <div class="foot-col foot-col--terms"><h4>Conditions</h4><ul><li>Delivery</li><li>Terms of Conditions</li><li>Privacy policy</li></ul></div>
  <div class="foot-rule"></div>
  <div class="copyright">Copyrights 2022 Glow Muse &nbsp;|&nbsp; All Rights Reserved</div>
  <div class="social"><i></i><i></i><i></i><i></i></div>
</section>

</body>
</html>
```